Qvx Brightforge Website

All the descriptions are available in the attached file. The designer has to structure the website and find the right images and icons. The website should look modern and avoid using images of real humans rather use animated images. Please note that the design should include home page, all the 4 services page , the contact us would be at the bottom of home page.

```html
<!DOCTYPE html>
<html lang="en">
<head>
<meta charset="utf-8">
<title>Qvx Brightforge</title>
<link href="https://fonts.googleapis.com/css2?family=Merienda:wght@700;800&family=Poppins:wght@400;500;600&display=swap" rel="stylesheet">
<style>
:root{
  --blue:#0b6fe0;
  --blue-soft:#cfe8f8;
  --blue-pale:#e4f3fc;
  --green:#55c500;
  --orange:#ff9a00;
  --ink:#111;
  --muted:#333;
  --white:#fff;
  --black:#000;
  --field-shadow:rgba(0,0,0,.14);
}
*{margin:0;padding:0;box-sizing:border-box}
html,body{width:1200px;height:3021px;overflow:hidden}
body{position:relative;background:var(--white);font-family:"Poppins",sans-serif;color:var(--ink)}
.abs{position:absolute}
.display{font-family:"Merienda",cursive;font-weight:800}
.accent{color:var(--blue)}

/* header */
.brand{left:117px;top:22px;display:flex;align-items:center;gap:10px;font-size:24px;font-weight:600;color:var(--blue);z-index:2}
.brand .mark{width:14px;height:14px;background:var(--blue)}
.nav{left:398px;top:34px;font-size:16px;z-index:2}
.nav a{color:var(--ink);text-decoration:none;position:absolute;white-space:nowrap}
.btn{background:var(--blue);color:var(--white);font-size:21px;display:flex;align-items:center;justify-content:center;border-radius:3px}
.header-btn{left:960px;top:25px;width:127px;height:42px;z-index:2}

/* hero */
.hero-band{left:0;top:0;width:1200px;height:829px;background:var(--white);box-shadow:0 6px 8px rgba(0,0,0,.12)}
.dot{border-radius:50%}
.hero-art{left:123px;top:395px;width:940px;height:580px;z-index:1}
.hero-title{left:0;top:88px;width:1200px;text-align:center;font-size:68px;line-height:86px;color:var(--blue);z-index:2}
.hero-sub{left:0;top:383px;width:1200px;text-align:center;font-size:23px;color:var(--ink);z-index:3}

/* services */
.section-title{left:0;width:1200px;text-align:center;font-size:38px;color:var(--ink)}
.services-intro{left:0;top:1128px;width:1200px;text-align:center;font-size:16.5px;line-height:26px;color:var(--muted)}
.service{width:294px;height:294px;border-radius:50%;background:var(--white);box-shadow:0 2px 10px rgba(0,0,0,.28);top:1223px;text-align:center}
.service svg.icon{position:absolute;left:110px;top:18px}
.service h3{position:absolute;top:114px;left:0;width:100%;font-size:21px;color:var(--ink)}
.service p{position:absolute;top:152px;left:22px;width:250px;font-size:16px;line-height:26px;color:var(--muted)}
.service .chev{position:absolute;left:136px;top:248px}
.pager{top:1556px;left:578px;display:flex;gap:6px}
.pager span{width:11px;height:11px;border-radius:50%;background:var(--ink)}

/* about */
.about-title{left:114px;top:1633px;font-size:37px}
.about-text{left:112px;top:1716px;width:375px;font-size:16px;line-height:25.8px;color:var(--muted)}
.about-text p+p{margin-top:25px}
.about-btn{left:113px;top:2069px;width:129px;height:42px;border-radius:6px}
.about-art{left:551px;top:1625px;width:540px;height:510px}

/* contact */
.footer-bg{left:0;top:2487px;width:1200px;height:534px;background:var(--black)}
.contact-card{left:113px;top:2215px;width:974px;height:360px;background:var(--white);box-shadow:0 0 10px rgba(0,0,0,.12)}
.field{width:433px;height:41px;background:var(--white);box-shadow:0 2px 6px var(--field-shadow);font-size:12px;padding-left:13px;display:flex;align-items:center;color:var(--ink)}
.submit{left:536px;top:2494px;width:128px;height:42px;border-radius:8px}

/* footer */
.footer-brand{left:0;top:2650px;width:1200px;display:flex;justify-content:center;align-items:center;gap:16px;font-size:56px;font-weight:600;color:var(--white)}
.footer-brand .mark{width:30px;height:30px;background:var(--white)}
.foot-col{top:2814px;color:var(--white)}
.foot-col h4{font-family:"Merienda",cursive;font-weight:800;font-size:24px;margin-bottom:10px}
.foot-col p{font-size:16.5px;line-height:34px}
.divider{left:0;top:2948px;width:1200px;height:1px;background:#555}
.copyright{left:0;top:2978px;width:1200px;text-align:center;font-size:12px;color:var(--white)}
</style>
</head>
<body>

<div class="abs hero-band"></div>

<!-- decorative circles -->
<div class="abs dot" style="left:-14px;top:80px;width:38px;height:30px;background:var(--blue);clip-path:inset(14px 0 0 0);border-radius:0 0 50% 50%"></div>
<div class="abs dot" style="left:1142px;top:32px;width:120px;height:120px;background:var(--green)"></div>
<div class="abs dot" style="left:922px;top:194px;width:10px;height:10px;background:var(--orange)"></div>
<div class="abs dot" style="left:-32px;top:379px;width:92px;height:88px;background:var(--orange)"></div>
<div class="abs dot" style="left:1126px;top:434px;width:31px;height:31px;background:var(--blue)"></div>
<div class="abs dot" style="left:135px;top:543px;width:26px;height:26px;background:var(--green)"></div>
<div class="abs dot" style="left:40px;top:770px;width:10px;height:10px;background:var(--green)"></div>
<div class="abs dot" style="left:279px;top:340px;width:10px;height:10px;background:var(--blue)"></div>
<div class="abs dot" style="left:1122px;top:680px;width:160px;height:150px;background:var(--orange)"></div>

<header>
  <div class="abs brand"><span class="mark"></span>Qvx Brightforge</div>
  <nav class="abs nav">
    <a style="left:0">Home</a>
    <a style="left:75px">Services</a>
    <a style="left:167px">Products</a>
    <a style="left:264px">Blog</a>
    <a style="left:326px">Contact US</a>
  </nav>
  <div class="abs btn header-btn">Contact Us</div>
</header>

<section>
  <svg class="abs hero-art" viewBox="0 0 940 580" role="img" aria-label="Illustration of two consultants at a desk reviewing analytics on a monitor">
    <defs><linearGradient id="heroGrad" x1="0" y1="0" x2="1" y2="1"><stop offset="0" stop-color="#d9eefa"/><stop offset="1" stop-color="#b9dff5"/></linearGradient></defs>
    <path d="M70 110 C140 30 300 60 440 40 C560 20 640 -10 730 20 C840 60 900 150 910 250 C915 340 860 380 900 460 C930 540 820 580 660 570 C500 560 330 585 190 560 C50 535 -10 430 5 320 C15 240 20 170 70 110Z" fill="url(#heroGrad)"/>
  </svg>
  <h1 class="abs hero-title display">Empower your digital<br>journey with our<br>advanced IT solutions.</h1>
  <p class="abs hero-sub display">From data to web and &nbsp;mobile apps, we've got you covered.</p>
</section>

<section>
  <h2 class="abs section-title display" style="top:1056px">Our <span class="accent">Services</span></h2>
  <p class="abs services-intro">We are a forward-thinking IT consulting firm specializing in providing cutting-edge<br>data analytics, web application development, and mobile app development services.</p>

  <article class="abs service" style="left:113px">
    <svg class="icon" width="74" height="74" viewBox="0 0 74 74" fill="none" stroke="var(--green)" stroke-width="2">
      <rect x="3" y="22" width="68" height="44"/><path d="M12 60V42M20 60V34M28 60V38M36 60V30"/><circle cx="58" cy="16" r="10"/><path d="M58 6v10h10"/><path d="M10 52l14-8 14 6 14-10 14 6"/><path d="M30 72h14"/>
    </svg>
    <h3 class="display">Data Analytics</h3>
    <p>Our data analytics consulting services help you unlock the full potential of your data.</p>
    <svg class="chev" width="20" height="28" viewBox="0 0 20 28"><path d="M5 3l10 11-10 11" stroke="var(--green)" stroke-width="3" fill="none"/></svg>
  </article>

  <article class="abs service" style="left:451px">
    <svg class="icon" width="74" height="74" viewBox="0 0 74 74" fill="none" stroke="var(--blue)" stroke-width="2">
      <rect x="3" y="4" width="64" height="52" rx="5"/><path d="M3 18h64"/><circle cx="13" cy="11" r="3"/><circle cx="23" cy="11" r="3"/><rect x="34" y="8" width="18" height="6" rx="3"/><path d="M18 30l-6 6 6 6M32 30l-6 14M38 30l6 6-6 6"/><circle cx="57" cy="56" r="9"/><circle cx="57" cy="56" r="4"/>
    </svg>
    <h3 class="display">Web Development</h3>
    <p>At Qvx Brightforge, we are a trailblazing web development company committed to.....</p>
    <svg class="chev" width="20" height="28" viewBox="0 0 20 28"><path d="M5 3l10 11-10 11" stroke="var(--blue)" stroke-width="3" fill="none"/></svg>
  </article>

  <article class="abs service" style="left:789px">
    <svg class="icon" width="74" height="74" viewBox="0 0 74 74" fill="none" stroke="var(--orange)" stroke-width="2">
      <path d="M37 4c8 6 10 16 8 26H29c-2-10 0-20 8-26z"/><circle cx="37" cy="18" r="4"/><path d="M29 30l-6 8h8M45 30l6 8h-8M33 38l4 8 4-8"/><path d="M8 56l14-8 12 8 8 0M66 56l-14-8-10 6"/><path d="M22 62l8 6M30 58l8 8"/>
    </svg>
    <h3 class="display">Start-up Partner</h3>
    <p>Let us join you on your journey to success and make a lasting impact together.</p>
    <svg class="chev" width="20" height="28" viewBox="0 0 20 28"><path d="M5 3l10 11-10 11" stroke="var(--orange)" stroke-width="3" fill="none"/></svg>
  </article>

  <div class="abs pager"><span></span><span></span><span></span></div>
</section>

<section>
  <h2 class="abs about-title display">About <span class="accent">Us</span></h2>
  <div class="abs about-text">
    <p>Our passion for innovation and technology drives us to deliver tailor-made solutions that empower businesses to thrive in the digital landscape.</p>
    <p>Our consultants boasts a wealth of experience across various technologies and industries, possessing both commercial insight and technical expertise. This enables us to provide tailor-made, innovative solutions that cater to your specific needs and objectives.</p>
  </div>
  <div class="abs btn about-btn">Read More</div>
  <svg class="abs about-art" viewBox="0 0 540 510" role="img" aria-label="Illustration of a team analysing bar charts under a large magnifying glass">
    <circle cx="270" cy="275" r="235" fill="var(--blue-soft)"/>
  </svg>
</section>

<div class="abs footer-bg"></div>

<section>
  <div class="abs contact-card"></div>
  <h2 class="abs section-title display" style="top:2251px">Contact <span class="accent">Us</span></h2>
  <div class="abs field" style="left:154px;top:2340px">Name</div>
  <div class="abs field" style="left:616px;top:2340px">Email</div>
  <div class="abs field" style="left:154px;top:2409px">Phone Number</div>
  <div class="abs field" style="left:616px;top:2409px;justify-content:space-between;padding-right:14px">Message
    <svg width="16" height="10" viewBox="0 0 16 10"><path d="M1 1l7 7 7-7" stroke="var(--ink)" stroke-width="1.5" fill="none"/></svg>
  </div>
  <div class="abs btn submit">Submit</div>
</section>

<footer>
  <div class="abs footer-brand"><span class="mark"></span>Qvx Brightforge</div>
  <div class="abs foot-col" style="left:114px"><h4>Address:</h4><p>Suite 12/40 Harlow Road,<br>Fernvale WA 6999</p></div>
  <div class="abs foot-col" style="left:537px"><h4>Phone:</h4><p>+61 (08) 5550 1234<br>(Sales / Support)</p></div>
  <div class="abs foot-col" style="left:897px"><h4>Email:</h4><p>hello@qvxbrightforge.com.au</p></div>
  <div class="abs divider"></div>
  <p class="abs copyright">Copyright © 2023 Qvx Brightforge. All rights reserved.</p>
</footer>

</body>
</html>
```